Payday Lending App Interface Design

Hello, we are building a payday lending application, Lendoro, that lend people money. I have drafted some of the screens that show the functionalities we have at the moment, please find the screens in attachments.
The elements in the screens are placed just to show what should be included in those screens, it's not necessary to follow the same layout. If you have better design ideas, you are very welcomed to show off your talent.
I think what we want is a style guide so that we can apply the same style to any screens that are similar to the ones I attached. We really like
the style as in the attached image called Style.png. We might want something similar - a simple, clean design yet fun and engaging. Customised graphical elements such as icons, illustrations are preferable.
Apart from the attached screens, we might also need a design for the On Board screen and the Login/Sign Up screen too.
Our logo colour is in yellow and black. Perhaps we will have a similar colour theme. I also attached the logo file, icon-Lendoro.png, if you would like to put it in your design.
Please message me if you need further information.
Regards
Target Market(s)
Young people that doesn't have strong income

```html
<!DOCTYPE html>
<html lang="en">
<head>
<meta charset="utf-8">
<title>Lendoro – App Screens</title>
<link rel="stylesheet" href="https://fonts.googleapis.com/css2?family=Rubik:wght@400;500;600&display=swap">
<style>
:root{
  --yellow:#fbd40b;
  --ink:#1c1c1c;
  --muted:#7a7a7a;
  --line:#e4e4e4;
  --nav:#efefef;
  --blue:#2a3bd0;
  --page:#f6f6fb;
  --card:#ffffff;
  --night-a:#15152b;
  --night-b:#3a1c4a;
}
*{box-sizing:border-box;margin:0;padding:0}
html,body{width:1200px;height:749px;overflow:hidden}
body{background:var(--page);font-family:"Rubik",sans-serif;color:var(--ink);position:relative}
.screen{position:absolute;top:76px;width:276px;height:593px;background:var(--card);overflow:hidden;border-radius:14px;box-shadow:0 10px 30px rgba(120,110,220,.14)}
.screen--details{left:87px}
.screen--loan{left:462px}
.screen--home{left:836px}
.abs{position:absolute}
.center{left:0;right:0;text-align:center}

.status{position:absolute;top:8px;left:22px;right:16px;display:flex;justify-content:space-between;color:#fff;font-size:11px;font-weight:500}
.navbar{position:absolute;left:0;right:0;bottom:0;height:42px;background:var(--nav);display:flex;justify-content:space-between;align-items:center;padding:0 16px}

.brand{display:flex;align-items:center;gap:6px;font-weight:600}
.brand__mark{width:14px;height:14px;background:var(--yellow);border-radius:2px}

.heading{font-size:19px;font-weight:500;letter-spacing:.2px}
.sub{font-size:11px}
.field{position:absolute;left:11px;width:254px;height:40px;border-radius:20px;background:#fff;box-shadow:0 3px 8px rgba(0,0,0,.12);font-size:11px;display:flex;align-items:center;justify-content:space-between;padding:0 16px}
.btn-next{position:absolute;left:11px;width:254px;top:438px;height:40px;border-radius:20px;background:var(--yellow);font-size:14px;font-weight:500;display:flex;align-items:center;justify-content:center;box-shadow:0 4px 8px rgba(251,212,11,.35)}

.hero-photo{position:absolute;top:0;left:0;right:0;height:193px;border-radius:0 0 14px 14px;background:linear-gradient(160deg,#4b4a45 0%,#2b2b2a 55%,#3c3a35 100%)}
.loan-title{top:52px;font-size:22px;font-weight:600;color:var(--yellow)}
.loan-next{top:83px;font-size:12px;color:#fff}
.loan-amount{top:101px;left:40px;font-size:35px;color:var(--yellow);font-weight:400}
.loan-amount small{font-size:13px;color:#fff;margin-left:4px}
.pill{position:absolute;top:182px;width:125px;height:36px;border-radius:18px;display:flex;align-items:center;justify-content:center;font-size:14px;font-weight:500;background:#fff;box-shadow:0 3px 8px rgba(0,0,0,.12)}
.pill--paid{left:10px;background:var(--yellow)}
.pill--left{left:140px}
.pill-label{position:absolute;top:224px;width:125px;text-align:center;font-size:11px;font-weight:500}
.section-title{position:absolute;top:274px;left:11px;font-size:15px;font-weight:500}
.activity{position:absolute;left:10px;width:255px;height:49px;background:#fff;border-radius:6px;box-shadow:0 2px 8px rgba(0,0,0,.1);display:flex;align-items:center;padding:0 9px;font-size:11px}
.activity span:nth-child(1){width:88px}
.activity span:nth-child(2){flex:1}
.activity span:nth-child(3){color:var(--blue)}
.footnote{position:absolute;left:11px;top:487px;width:195px;font-size:9px;line-height:16px;color:#333}
.foot-brand{position:absolute;left:205px;top:505px;font-size:11px}

.hero-night{position:absolute;top:0;left:0;right:0;height:189px;background:linear-gradient(180deg,var(--night-a) 0%,#251a3c 55%,var(--night-b) 100%)}
.greet{top:90px;color:#fff;font-size:15px}
.greet-name{top:112px;color:#fff;font-size:17px;font-weight:500}
.task{position:absolute;left:18px;width:253px;height:62px;background:#fff;border-radius:4px;box-shadow:0 3px 10px rgba(0,0,0,.1);display:flex;align-items:center;padding:4px}
.task__icon{width:47px;height:52px;background:#f1f1f1;border-radius:2px;display:flex;align-items:center;justify-content:center;flex:none}
.task__body{flex:1;padding-left:9px}
.task__title{font-size:13px;line-height:15px}
.task__desc{font-size:10px;color:var(--muted);line-height:13px;margin-top:3px}
.task__check{width:19px;height:19px;border-radius:50%;background:var(--yellow);display:flex;align-items:center;justify-content:center;margin-right:12px;flex:none;box-shadow:0 2px 4px rgba(0,0,0,.2)}
.ghost{position:absolute;top:473px;width:110px;height:44px;border:1px solid var(--line);border-radius:4px;display:flex;align-items:center;justify-content:center;font-size:11px;color:#aaa}
</style>
</head>
<body>

<!-- Personal details -->
<section class="screen screen--details">
  <div class="abs center" style="top:64px;display:flex;justify-content:center">
    <div class="brand" style="font-size:22px"><span class="brand__mark" style="width:22px;height:22px"></span>Lendoro</div>
  </div>
  <h1 class="abs center heading" style="top:155px">PERSONAL DETAILS</h1>
  <p class="abs center sub" style="top:184px">Please Provide details as shown on ID</p>
  <div class="field" style="top:228px">Given Name</div>
  <div class="field" style="top:276px">Middle Name</div>
  <div class="field" style="top:327px">Surname</div>
  <div class="field" style="top:377px">Date of Birth
    <svg width="11" height="11" viewBox="0 0 11 11" fill="none" stroke="#333" stroke-width="1"><rect x="1" y="2" width="9" height="8"/><path d="M1 4.5h9M3.5 1v2M7.5 1v2M3.5 6.5h1M6.5 6.5h1M3.5 8.5h1M6.5 8.5h1"/></svg>
  </div>
  <div class="btn-next">Next</div>
  <nav class="navbar">
    <svg width="12" height="12" viewBox="0 0 12 12" fill="none" stroke="#444"><path d="M10 1L2 6l8 5z"/></svg>
    <svg width="12" height="12" viewBox="0 0 12 12" fill="none" stroke="#444"><circle cx="6" cy="6" r="5"/></svg>
    <svg width="12" height="12" viewBox="0 0 12 12" fill="none" stroke="#444"><rect x="1" y="1" width="10" height="10" rx="2"/></svg>
  </nav>
</section>

<!-- Loan details -->
<section class="screen screen--loan">
  <div class="hero-photo" role="img" aria-label="Photo of a smiling man reading a letter on a sofa"></div>
  <div class="status"><span>9:30</span><span>▮▮ ◠ ▭</span></div>
  <h1 class="abs center loan-title">Loan Details</h1>
  <p class="abs center loan-next">Next Repayments</p>
  <p class="abs loan-amount">$150.00<small>On 4 DEc</small></p>
  <div class="pill pill--paid">$200.00</div>
  <div class="pill pill--left">$500.00</div>
  <div class="pill-label" style="left:10px">Paid</div>
  <div class="pill-label" style="left:140px">Left</div>
  <h2 class="section-title">Activities</h2>
  <div class="activity" style="top:300px"><span>Repayment</span><span>10-Jan-2022</span><span>$200.00</span></div>
  <div class="activity" style="top:356px"><span>Repayment</span><span>10-Jan-2022</span><span>$200.00</span></div>
  <div class="activity" style="top:411px"><span>Repayment</span><span>10-Jan-2022</span><span>$200.00</span></div>
  <p class="footnote">Lorem ipsum dolor sit amet, consectetur adipiscing elit, sed do incididunt ut labore et dolore magna aliqua.</p>
  <div class="brand foot-brand"><span class="brand__mark" style="width:10px;height:10px"></span>Lendoro</div>
  <nav class="navbar">
    <svg width="12" height="12" viewBox="0 0 12 12" fill="none" stroke="#444"><path d="M10 1L2 6l8 5z"/></svg>
    <svg width="12" height="12" viewBox="0 0 12 12" fill="none" stroke="#444"><circle cx="6" cy="6" r="5"/></svg>
    <svg width="12" height="12" viewBox="0 0 12 12" fill="none" stroke="#444"><rect x="1" y="1" width="10" height="10" rx="2"/></svg>
  </nav>
</section>

<!-- Home / progress -->
<section class="screen screen--home">
  <div class="hero-night" role="img" aria-label="Dark purple header with a faint hexagon network pattern"></div>
  <div class="status"><span>9:30</span><span>▮▮ ◠ ▭</span></div>
  <svg class="abs" style="left:18px;top:31px" width="14" height="11" viewBox="0 0 14 11" stroke="#fff" stroke-width="1.3"><path d="M0 1h14M0 5.5h14M0 10h14"/></svg>
  <div class="abs center" style="top:28px;display:flex;justify-content:center">
    <div class="brand" style="color:#fff;font-size:13px"><span class="brand__mark"></span>Lendoro</div>
  </div>
  <svg class="abs" style="right:14px;top:29px" width="15" height="15" viewBox="0 0 15 15" fill="none" stroke="#fff" stroke-width="1.4"><circle cx="6" cy="6" r="5"/><path d="M10 10l4 4"/></svg>
  <p class="abs center greet">Hi</p>
  <p class="abs center greet-name">Mara Quillon</p>

  <div class="task" style="top:157px">
    <div class="task__icon"><svg width="28" height="28" viewBox="0 0 28 28" fill="none" stroke="#222" stroke-width="1.3"><path d="M11 17c2-7 7-13 15-15-2 8-8 13-15 15z"/><path d="M11 17l-4-1 4-5h4M11 17l1 4 5-4v-4"/><circle cx="19" cy="9" r="2"/><path d="M7 21l-4 4M9 23l-3 3M5 19l-3 3"/></svg></div>
    <div class="task__body"><div class="task__title">Start</div><div class="task__desc">Lorem ipsum dolor sit amet,<br>consectetur adipiscing</div></div>
    <div class="task__check"><svg width="9" height="7" viewBox="0 0 9 7" fill="none" stroke="#222" stroke-width="1.6"><path d="M1 3.5l2.5 2.5L8 1"/></svg></div>
  </div>
  <div class="task" style="top:228px">
    <div class="task__icon"><svg width="28" height="30" viewBox="0 0 28 30" fill="none" stroke="#222" stroke-width="1.4"><circle cx="14" cy="9" r="6"/><path d="M3 28v-4c0-4 3-7 7-7h8c4 0 7 3 7 7v4z"/></svg></div>
    <div class="task__body"><div class="task__title">Upload your personal<br>info</div><div class="task__desc">Lorem ipsum dolor sit amet,</div></div>
    <div class="task__check"><svg width="9" height="7" viewBox="0 0 9 7" fill="none" stroke="#222" stroke-width="1.6"><path d="M1 3.5l2.5 2.5L8 1"/></svg></div>
  </div>
  <div class="task" style="top:300px">
    <div class="task__icon"><svg width="34" height="30" viewBox="0 0 34 30" fill="none" stroke="#222" stroke-width="1.2"><path d="M2 9L17 2l15 7zM3 11h28M3 27h28M1 29h32"/><path d="M6 13v12M10 13v12M14 13v12M20 13v12M24 13v12M28 13v12"/><text x="14" y="9" font-size="5" fill="#222" stroke="none">$</text></svg></div>
    <div class="task__body"><div class="task__title">Connect Bank Account</div><div class="task__desc">Lorem ipsum dolor sit amet,<br>consectetur adipiscing</div></div>
    <div class="task__check"><svg width="9" height="7" viewBox="0 0 9 7" fill="none" stroke="#222" stroke-width="1.6"><path d="M1 3.5l2.5 2.5L8 1"/></svg></div>
  </div>
  <div class="task" style="top:371px">
    <div class="task__icon"><svg width="32" height="32" viewBox="0 0 32 32" fill="none" stroke="#222" stroke-width="1.3"><path d="M7 4h14l6 6v18H7z"/><path d="M21 4v6h6"/><circle cx="11" cy="9" r="1.5"/><circle cx="12" cy="21" r="6" fill="#f1f1f1"/><text x="9.3" y="24.5" font-size="9" fill="#222" stroke="none">$</text><path d="M20 18h4M20 21h4M20 24h4"/></svg></div>
    <div class="task__body"><div class="task__title">Apply Loan</div><div class="task__desc">Lorem ipsum dolor sit amet,<br>consectetur adipiscing</div></div>
    <div class="task__check"><svg width="9" height="7" viewBox="0 0 9 7" fill="none" stroke="#222" stroke-width="1.6"><path d="M1 3.5l2.5 2.5L8 1"/></svg></div>
  </div>

  <div class="ghost" style="left:31px">Repayments</div>
  <div class="ghost" style="left:147px">Loan Closed</div>
  <nav class="navbar">
    <svg width="12" height="12" viewBox="0 0 12 12" fill="none" stroke="#444"><path d="M10 1L2 6l8 5z"/></svg>
    <svg width="12" height="12" viewBox="0 0 12 12" fill="none" stroke="#444"><circle cx="6" cy="6" r="5"/></svg>
    <svg width="12" height="12" viewBox="0 0 12 12" fill="none" stroke="#444"><rect x="1" y="1" width="10" height="10" rx="2"/></svg>
  </nav>
</section>

</body>
</html>
```